A Spin Above Par Company Brochure

I am the owner of a Mobile Disc Jockey company specializing in weddings. I am looking for a Tri Fold color brochure that is modern and eye catching with the focus being on upscale wedding events. I also want it to be easy to read and not overly cluttered ! I would like it to reflect our website located at aspinabovepar.example
I also have different variations and file types of my logo such as jpeg and png files. I need some good dance floor pics. If you do not have any good stock photos I can look through my photo library. I uploaded a logo and pic I found from one of my videos. Not sure if it is worth anything.
We also do Uplighting and Photo Booths which I would like in the brochure. Much of the text copy needed can be taken from our website if needed. Please refer to the website to see what we do and our style.

Target Market(s)

upscale weddings

Industry/Entity Type

wedding dj entertainment & masters of ceremonies

Requirements
Nice to have
• nice pictures of packed dance floors and people having fun

```html
<!DOCTYPE html>
<html lang="en">
<head>
<meta charset="utf-8">
<title>A Spin Above Par — Tri-Fold Brochure</title>
<link href="https://fonts.googleapis.com/css2?family=Montserrat:wght@400;500;600;700;800&family=Oswald:wght@500;600&display=swap" rel="stylesheet">
<style>
  :root{
    --purple:#7a2896;
    --purple-deep:#5a1772;
    --purple-soft:#9b4cb8;
    --gold:#f7c21a;
    --grey:#8b8b8e;
    --grey-dark:#5d5d60;
    --white:#ffffff;
    --ink:#3a3a3c;
    --page:#ffffff;
  }
  *{margin:0;padding:0;box-sizing:border-box}
  html,body{width:1200px;height:2245px;overflow:hidden;background:var(--page)}
  body{position:relative;font-family:"Montserrat",Arial,sans-serif;color:var(--white)}
  .spread{position:absolute;left:60px;width:1080px;height:834px;overflow:hidden;background:var(--white);box-shadow:0 6px 18px rgba(0,0,0,.25)}
  .spread--outside{top:260px}
  .spread--inside{top:1154px}
  .spread__art{position:absolute;inset:0;width:100%;height:100%}
  .abs{position:absolute}
  .brand{display:flex;align-items:center;gap:8px;font-weight:700;font-size:21px;letter-spacing:.2px;white-space:nowrap}
  .brand__dot{width:16px;height:16px;border-radius:50%;background:currentColor}
  .brand--light{color:var(--white)}
  .brand--dark{color:var(--purple)}
  .dots{display:flex;gap:4px}
  .dots span{width:6px;height:6px;border-radius:50%;background:var(--white)}
  .dots span:last-child{opacity:.5}
  .url{white-space:nowrap}

  /* outside */
  .intro__title{left:38px;top:32px;font-size:28px;font-weight:600}
  .intro__lead{left:38px;top:70px;width:320px;font-size:18px;font-weight:600;line-height:1.2}
  .intro__body{left:38px;top:140px;width:285px;font-size:13px;line-height:1.17}
  .intro__body p+p{margin-top:16px}
  .contact__brand{left:406px;top:376px}
  .cta__strong{font-weight:800;color:var(--gold);font-size:23px;line-height:1.2}
  .cta__soft{font-weight:500;color:var(--gold);font-size:23px;line-height:1.2}
  .contact__cta{left:404px;top:484px}
  .contact__call{left:404px;top:564px;font-size:15px;font-weight:500}
  .contact__phone{left:404px;top:584px;font-size:23px;font-weight:600;display:flex;align-items:center;gap:8px}
  .contact__line{left:404px;font-size:12.5px;display:flex;align-items:flex-start;gap:10px;line-height:1.25;white-space:nowrap}
  .contact__line svg{flex:none;margin-top:2px}
  .contact__hours{left:404px;top:696px;font-size:12px;line-height:1.4}
  .contact__hours b{font-weight:500;font-size:14px}
  .contact__web{left:404px;top:740px;font-size:12px;font-weight:500}
  .contact__rule{left:404px;top:768px;width:32px;height:2px;background:var(--white)}
  .contact__follow{left:404px;top:778px;font-size:13px;display:flex;align-items:center;gap:6px}
  .social{width:15px;height:15px;border-radius:50%;background:var(--white)}
  .cover__brand{right:46px;top:548px}
  .cover__headline{right:40px;top:608px;text-align:right;font-family:"Oswald",Arial,sans-serif;color:var(--purple);font-weight:600;font-size:60px;line-height:1;letter-spacing:-.5px}
  .cover__sub{right:40px;top:735px;font-family:"Oswald",Arial,sans-serif;color:var(--ink);font-weight:500;font-size:27px;letter-spacing:-.3px}
  .cover__web{right:40px;top:790px;color:var(--purple);font-size:13.5px;font-weight:600;letter-spacing:.3px}

  /* inside */
  .panel__title{font-weight:700;font-size:40px;line-height:1}
  .panel__text{font-size:17px;line-height:1.18}
  .weddings{left:40px;top:42px;width:225px}
  .weddings .panel__text{margin-top:16px}
  .weddings .dots{margin-top:20px}
  .corporate{left:395px;top:598px;width:285px}
  .corporate .panel__title{font-size:34px;line-height:1.05}
  .corporate .panel__title span{font-size:31px}
  .corporate .panel__text{margin-top:14px;font-size:15px}
  .corporate .dots{margin-top:18px}
  .booth{left:842px;top:46px;width:210px}
  .booth .panel__title{font-size:37px;line-height:1}
  .booth .panel__title span{font-weight:500}
  .booth .panel__text{margin-top:16px}
  .booth .dots{margin-top:16px}
  .booth__brand{left:832px;top:642px}
  .booth__cta{left:764px;top:704px;width:313px;text-align:center}
  .booth__web{left:780px;top:770px;width:290px;height:36px;border-radius:4px;background:var(--gold);color:var(--purple);font-weight:700;font-size:14.5px;letter-spacing:.8px;display:flex;align-items:center;justify-content:center;white-space:nowrap}
</style>
</head>
<body>

<section class="spread spread--outside">
  <svg class="spread__art" viewBox="0 0 862 666" preserveAspectRatio="none">
    <defs>
      <linearGradient id="partyFade" x1="0" y1="0" x2="0" y2="1">
        <stop offset="0" stop-color="#7a2896"/>
        <stop offset=".35" stop-color="#8a4a8e"/>
        <stop offset=".7" stop-color="#6b4a4a"/>
        <stop offset="1" stop-color="#3d2a2c"/>
      </linearGradient>
      <linearGradient id="coupleFade" x1="0" y1="0" x2=".3" y2="1">
        <stop offset="0" stop-color="#3b2a30"/>
        <stop offset=".45" stop-color="#8a6a7a"/>
        <stop offset=".8" stop-color="#c9b8c4"/>
        <stop offset="1" stop-color="#ece6ea"/>
      </linearGradient>
      <linearGradient id="contactPanel" x1="0" y1="0" x2="0" y2="1">
        <stop offset="0" stop-color="#7a2896" stop-opacity=".2"/>
        <stop offset=".35" stop-color="#7a2896" stop-opacity=".95"/>
        <stop offset="1" stop-color="#7a2896"/>
      </linearGradient>
      <linearGradient id="coverWhite" x1="0" y1="0" x2="0" y2="1">
        <stop offset="0" stop-color="#fff" stop-opacity="0"/>
        <stop offset=".35" stop-color="#fff" stop-opacity=".92"/>
        <stop offset="1" stop-color="#fff"/>
      </linearGradient>
    </defs>
    <path role="img" aria-label="Photo: guests and bride dancing on a packed wedding dance floor" d="M0 0H425L562 340L455 666H0Z" fill="url(#partyFade)"/>
    <path d="M0 0H330V110H0Z" fill="#7a2896" opacity=".85"/>
    <path d="M300 270H548L562 340L455 666H270Z" fill="url(#contactPanel)"/>
    <path role="img" aria-label="Photo: bride and groom walking through confetti and sharing a first dance" d="M440 0H862V666H600L582 340Z" fill="url(#coupleFade)"/>
    <path d="M600 300H862V666H560Z" fill="url(#coverWhite)"/>
    <path d="M415 0H440L585 340L478 666H453L560 340Z" fill="#fff"/>
    <path d="M590 410H622L530 666H498Z" fill="var(--grey)"/>
    <path d="M622 410H640L548 666H530Z" fill="#fff"/>
    <path d="M628 520L650 666H575Z" fill="var(--purple)"/>
  </svg>

  <h1 class="abs intro__title">It’s your day</h1>
  <p class="abs intro__lead">Let us help you make it happen, your way</p>
  <div class="abs intro__body">
    <p>It’s your day. Let us help you make it happen, your way. Our award winning DJs are recommended by the finest venues in Palm Shores, Bayview and the surrounding areas and we are known for helping our clients create the ultimate wedding entertainment experience.</p>
    <p>We offer creative ideas and a fresh approach to help you customize your event around the style &amp; vibe that you want. Planning this way is fun and eliminates the stress that comes with preparing for your special day.</p>
  </div>

  <div class="abs brand brand--light contact__brand"><span class="brand__dot"></span>A Spin Above Par</div>
  <div class="abs contact__cta"><div class="cta__strong">Book Your</div><div class="cta__soft">Appointment Today</div></div>
  <div class="abs contact__call">Call Us Today</div>
  <div class="abs contact__phone">
    <svg width="16" height="16" viewBox="0 0 24 24"><path fill="#fff" d="M6.6 10.8a15 15 0 0 0 6.6 6.6l2.2-2.2a1 1 0 0 1 1-.25 11.4 11.4 0 0 0 3.6.57 1 1 0 0 1 1 1V20a1 1 0 0 1-1 1A17 17 0 0 1 3 4a1 1 0 0 1 1-1h3.5a1 1 0 0 1 1 1c0 1.25.2 2.45.57 3.57a1 1 0 0 1-.25 1Z"/></svg>
    555.010.4827
  </div>
  <div class="abs contact__line" style="top:626px">
    <svg width="12" height="10" viewBox="0 0 24 18"><rect x="1" y="1" width="22" height="16" fill="none" stroke="#fff" stroke-width="2"/><path d="M1 1l11 9 11-9" fill="none" stroke="#fff" stroke-width="2"/></svg>
    hello@aspinabovepar.example
  </div>
  <div class="abs contact__line" style="top:650px">
    <svg width="12" height="14" viewBox="0 0 24 28"><path fill="#fff" d="M12 0a10 10 0 0 0-10 10c0 7.5 10 18 10 18s10-10.5 10-18A10 10 0 0 0 12 0Zm0 14a4 4 0 1 1 0-8 4 4 0 0 1 0 8Z"/></svg>
    <span>A Spin Above Par Palm Shores,<br>FL 34000</span>
  </div>
  <div class="abs contact__hours">Monday - Friday:<br><b>8:00 AM - 10:00 PM</b></div>
  <div class="abs url contact__web">www.aspinabovepar.example</div>
  <div class="abs contact__rule"></div>
  <div class="abs contact__follow">Follow Us <span class="social"></span><span class="social"></span></div>

  <div class="abs brand brand--dark cover__brand"><span class="brand__dot"></span>A Spin Above Par</div>
  <div class="abs cover__headline">MODERN,<br>TASTEFUL</div>
  <div class="abs cover__sub">&amp; FUN ENTERTAINMENT</div>
  <div class="abs url cover__web">www.aspinabovepar.example</div>
</section>

<section class="spread spread--inside">
  <svg class="spread__art" viewBox="0 0 862 666" preserveAspectRatio="none">
    <defs>
      <linearGradient id="weddingFade" x1="0" y1="0" x2="0" y2="1">
        <stop offset="0" stop-color="#7a2896"/>
        <stop offset=".25" stop-color="#7a2896"/>
        <stop offset=".45" stop-color="#8a5a6a"/>
        <stop offset=".75" stop-color="#4a3a3a"/>
        <stop offset="1" stop-color="#2e2628"/>
      </linearGradient>
      <linearGradient id="floorFade" x1="0" y1="0" x2="0" y2="1">
        <stop offset="0" stop-color="#3a2a4a"/>
        <stop offset=".35" stop-color="#5a3a8a"/>
        <stop offset=".65" stop-color="#6a5a7a"/>
        <stop offset="1" stop-color="#5a5a5e"/>
      </linearGradient>
      <linearGradient id="corpGrey" x1="0" y1="0" x2="0" y2="1">
        <stop offset="0" stop-color="#7d7d80" stop-opacity="0"/>
        <stop offset=".4" stop-color="#7d7d80" stop-opacity=".95"/>
        <stop offset="1" stop-color="#7d7d80"/>
      </linearGradient>
      <linearGradient id="boothFade" x1="0" y1="0" x2="0" y2="1">
        <stop offset="0" stop-color="#7a2896"/>
        <stop offset=".28" stop-color="#7a2896"/>
        <stop offset=".45" stop-color="#6a4a6e"/>
        <stop offset=".65" stop-color="#5a4a5a"/>
        <stop offset=".82" stop-color="#7a2896"/>
        <stop offset="1" stop-color="#7a2896"/>
      </linearGradient>
    </defs>
    <path role="img" aria-label="Photo: bride and groom laughing as they enter the reception" d="M0 0H330L258 666H0Z" fill="url(#weddingFade)"/>
    <path role="img" aria-label="Photo: packed dance floor with guests raising their hands under a chandelier" d="M330 0H672L548 666H258Z" fill="url(#floorFade)"/>
    <path d="M290 380H610L548 666H258Z" fill="url(#corpGrey)"/>
    <path role="img" aria-label="Photo: wedding guests posing in a photo booth with props and chalkboard signs" d="M672 0H862V666H548Z" fill="url(#boothFade)"/>
    <path d="M302 0H312L240 666H230Z" fill="var(--grey)"/>
    <path d="M316 0H328L256 666H244Z" fill="#fff"/>
    <path d="M660 0H672L548 666H536Z" fill="#fff"/>
  </svg>

  <div class="abs weddings">
    <h2 class="panel__title">Weddings</h2>
    <p class="panel__text">Wedding entertainment planning &amp; coordination the way you want it</p>
    <div class="dots"><span></span><span></span><span></span><span></span></div>
  </div>

  <div class="abs corporate">
    <h2 class="panel__title">Corporate<br><span>DJ Entertainment</span></h2>
    <p class="panel__text">A Spin Above Par has been entertaining at corporate events, trade shows and company parties for over 29 years.</p>
    <div class="dots"><span></span><span></span><span></span><span></span></div>
  </div>

  <div class="abs booth">
    <h2 class="panel__title">Photo<br><span>Booth</span></h2>
    <p class="panel__text">It’s no secret photo booths have been a hit at weddings as well as any other event.</p>
    <div class="dots"><span></span><span></span><span></span><span></span></div>
  </div>

  <div class="abs brand brand--light booth__brand"><span class="brand__dot"></span>A Spin Above Par</div>
  <div class="abs booth__cta"><div class="cta__strong">Book Your</div><div class="cta__soft">Appointment Today</div></div>
  <div class="abs booth__web">www.aspinabovepar.example</div>
</section>

</body>
</html>
```